Hardcore nerd needs to stand out in a sea of dull Defence business cards

Wombarra Devices is a new Australian consulting engineering company that turns research and theory into practical systems. No evangelistic fluff, just mathematics and physics into electronic and optical circuits for consumer products, scientific research or Defence applications.

We already have a recognised logo (provided) which is often dark blue/black on a light background but we're open to other combinations. (Us engineers tend to have limited aesthetic imagination :)

Some of our recent products have included:
* Instrumentation for electrical testing,
* Radar jammers,
* GPS antenna design,
* Satellite tracking systems,
* High power lasers

We're open to both single and double-sided designs - happy to be convinced either way.

P.S. Another group is working on the web page, so - alas - our web site is currently of no use for images/ideas...

Target Market(s)

Engineering managers,
Scientists

Contact Information for Business Card

Dr Colin Harte
R&D Engineer

colin@wombarradevices.com.au
0427 563 710

PO Box XXX (to be confirmed)
Kelsby ACT 2917
Australia

Font styles to use
Serif
Sans Serif

Colors

Designer to choose colors to be used in the design.

Requirements
Must have
• My contact details!
• I've had many (great) "bold and plain" designs submitted already, so feel free to be artistically creative :)
• Happy to take advice re fonts/colours/printability etc.
Nice to have
• I'm not sure if "lists" are more at home on a CV than a business card, but representative services include:
• Applied electromagnetics
• RF and high speed electronics
• Signal and image processing
• Electro-optical and laser systems
• Concept-to-prototype design services
• If you're considering double sided cards, then often measuring/alignment grids/rulers feature on the back of similar cards.
• e.g. https://www.veltranoptics.example/newgrouppage9.cfm?objectgroup_id=4183
• https://www.veltranoptics.example/newgrouppage9.cfm?objectgroup_ID=4185
• ..or even a "Smith chart" (google will return lots)
• Generic images to represent a capability might work - googling images associated with keyword for each of these areas might help:
• - "passive radar", "phased array", "fdtd", "vircator"
• RF and high speed electronic design
• - "smith chart", "microstrip circuits", "dimensioned drawing", "electronic schematic"
• - "dft", "iir filter"
• - "optical cavity". "laser energy level diagram"
• Background/watermarked images outlines/wireframes/schematics would probably look OK.
Should not have
• If a list of projects/services is provided, it is important not to make the client feel that this is "all" the company can do. Engineering design is a creative discipline (like graphics :)
• Please, no stock "military" snaps like planes, missiles, etc!

```html
<!DOCTYPE html>
<html lang="en">
<head>
<meta charset="utf-8">
<title>Wombarra Devices – Business Card</title>
<link rel="stylesheet" href="https://fonts.googleapis.com/css2?family=Arimo:wght@700&family=Lato:wght@400;700&display=swap">
<style>
  :root {
    --navy: #041f5e;
    --white: #ffffff;
    --rule: #3a5596;
    --backdrop: #d9d9d9;
  }
  * { margin: 0; padding: 0; box-sizing: border-box; }
  html, body { width: 1200px; height: 802px; overflow: hidden; }
  body {
    position: relative;
    background: var(--backdrop);
    font-family: "Lato", Arial, sans-serif;
  }
  .card {
    position: absolute;
    top: 274px;
    width: 442px;
    height: 264px;
    overflow: hidden;
  }
  .card--front { left: 136px; background: var(--white); }
  .card--back { left: 624px; background: var(--navy); }

  .front-band {
    position: absolute;
    left: 0; right: 0; top: 106px; bottom: 0;
    background: var(--navy);
  }
  .front-stripe {
    position: absolute;
    left: 0; right: 0; top: 120px; height: 4px;
    background: var(--white);
  }
  .brand {
    position: absolute;
    display: flex;
    align-items: center;
    gap: 10px;
    font-family: "Lato", Arial, sans-serif;
    font-weight: 700;
    letter-spacing: 1px;
    white-space: nowrap;
  }
  .brand__dot { border-radius: 50%; flex: none; }
  .brand--front {
    left: 50%; top: 38px; transform: translateX(-50%);
    color: var(--navy); font-size: 20px;
  }
  .brand--front .brand__dot { width: 26px; height: 26px; background: var(--navy); }
  .brand--back {
    left: 50%; top: 50%; transform: translate(-50%, -50%);
    color: var(--white); font-size: 26px;
  }
  .brand--back .brand__dot { width: 40px; height: 40px; background: var(--white); }

  .contact {
    position: absolute;
    left: 0; right: 0; top: 140px;
    text-align: center;
    color: var(--white);
  }
  .contact__name {
    font-family: "Arimo", Arial, sans-serif;
    font-weight: 700;
    font-size: 16px;
    line-height: 20px;
  }
  .contact__role { font-size: 12px; line-height: 15px; }
  .contact__rule {
    width: 144px; height: 1px;
    margin: 4px auto 6px;
    background: var(--rule);
  }
  .contact__line { font-size: 12px; line-height: 16px; }
  .contact__address { font-size: 12px; line-height: 16px; }
</style>
</head>
<body>
  <section class="card card--front" aria-label="Business card front">
    <div class="brand brand--front">
      <span class="brand__dot"></span>
      <span class="brand__name">WOMBARRA DEVICES</span>
    </div>
    <div class="front-band"></div>
    <div class="front-stripe"></div>
    <div class="contact">
      <p class="contact__name">DR COLIN HARTE</p>
      <p class="contact__role">R&amp;D Engineer</p>
      <div class="contact__rule"></div>
      <p class="contact__line">0427 563 710</p>
      <p class="contact__line">colin@wombarradevices.com.au</p>
      <div class="contact__rule"></div>
      <p class="contact__address">PO Box XXX&nbsp; Kelsby ACT 2917, Australia</p>
    </div>
  </section>

  <section class="card card--back" aria-label="Business card back">
    <div class="brand brand--back">
      <span class="brand__dot"></span>
      <span class="brand__name">WOMBARRA DEVICES</span>
    </div>
  </section>
</body>
</html>
```